Communication and Marketing agency needs a new presentation card

We are a group of communication and marketing agencies specialized in companies that are in the logistics and industrial sector. The head agency is TELVANO Grupo and the group consists of 4 agencies: TELVANO Media, TELVANO Digital, TELVANO Research and DifundeEnPantalla. We hace 4 offices in Spain (Madrid, Barcelona, Valencia and Murcia). We are looking for a clean and attractive design that transmits our experience, brand presence in the market and knowledge to those who receive the card.It has to maintain the colors of the logo that is attached.
Target Market(s)
logistics and industrial sector
Marketing department
Contact Information for Business Card
Clean and attractive design

```html
<!DOCTYPE html>
<html lang="en">
<head>
<meta charset="utf-8">
<title>TELVANO Grupo – Business Card</title>
<link rel="stylesheet" href="https://fonts.googleapis.com/css2?family=Oswald:wght@500&family=PT+Sans:wght@400;700&display=swap">
<style>
  :root {
    --stage: #2b2b2b;
    --card: #1c1c1d;
    --red: #c1272d;
    --silver: #d4d4d6;
    --grey: #5c5c5e;
    --white: #f2f2f2;
  }
  * { margin: 0; padding: 0; box-sizing: border-box; }
  html, body { width: 1200px; height: 900px; overflow: hidden; }
  body {
    background: var(--stage);
    font-family: "PT Sans", Arial, sans-serif;
    color: var(--white);
    position: relative;
  }
  .card {
    position: absolute;
    left: 250px;
    width: 700px;
    height: 400px;
    background: var(--card);
    box-shadow: 0 10px 30px rgba(0,0,0,.45);
  }
  .card--front { top: 35px; }
  .card--back { top: 465px; }

  .brand-name {
    position: absolute;
    font-family: "Oswald", "Arial Narrow", sans-serif;
    font-weight: 500;
    text-transform: none;
    line-height: 1;
    letter-spacing: 2px;
    text-align: right;
  }
  .card--front .brand-name {
    right: 150px;
    top: 140px;
    font-size: 64px;
    color: var(--silver);
  }
  .card--back .brand-name {
    right: 70px;
    top: 70px;
    font-size: 60px;
    color: var(--red);
  }
  .brand-name small {
    display: block;
    font-size: 34px;
    letter-spacing: 1px;
    margin-top: 4px;
  }

  .person {
    position: absolute;
    left: 60px;
    top: 168px;
  }
  .person__name {
    font-family: "Oswald", "Arial Narrow", sans-serif;
    font-weight: 500;
    font-size: 30px;
    color: var(--red);
    text-transform: uppercase;
    line-height: 1.05;
  }
  .person__role {
    font-size: 15px;
    letter-spacing: 1px;
    text-transform: uppercase;
  }

  .divider {
    display: block;
    width: 40px;
    height: 8px;
    margin: 10px 0 12px;
  }

  .contact {
    font-size: 16px;
    line-height: 1.35;
  }
  .contact b { font-weight: 700; margin-right: 4px; }

  .address {
    position: absolute;
    right: 60px;
    bottom: 40px;
    font-size: 16px;
    line-height: 1.35;
  }
  .address .divider { margin-top: 0; }
  .address__web span { color: var(--red); }
</style>
</head>
<body>

  <section class="card card--front" aria-label="Card front">
    <div class="brand-name">TELVANO<small>Digital</small></div>
  </section>

  <section class="card card--back" aria-label="Card back">
    <div class="brand-name">TELVANO<small>Grupo</small></div>

    <div class="person">
      <div class="person__name">Mara Velden</div>
      <div class="person__role">Manager</div>
      <svg class="divider" viewBox="0 0 40 8" aria-hidden="true">
        <circle cx="4" cy="4" r="3.5" fill="var(--red)"/>
        <line x1="4" y1="4" x2="40" y2="4" stroke="var(--red)" stroke-width="1.5"/>
      </svg>
      <div class="contact">
        <div><b>P.</b>+(555) -214- 6093</div>
        <div><b>F.</b>+(555) -214- 6093</div>
        <div>hello@velnorte.com</div>
      </div>
    </div>

    <div class="address">
      <svg class="divider" viewBox="0 0 40 8" aria-hidden="true">
        <circle cx="4" cy="4" r="3.5" fill="var(--red)"/>
        <line x1="4" y1="4" x2="40" y2="4" stroke="var(--red)" stroke-width="1.5"/>
      </svg>
      <div>480 Harlow Avenue,</div>
      <div>Linden, NE 68000</div>
      <div class="address__web">www.<span>telvanogrupo</span>.com</div>
    </div>
  </section>

</body>
</html>
```